Business card design needed

I would like a one sided black business card with the information provided above. Refer to my website www.brightvolleyracquets.com.au for an example of colors I have used for my site, would like to keep this consistent for my business cards also, I will upload my logo below.

I am a new small business that provides tennis customers with racquet re stringing, tennis strings and accessories.

Industry/Entity Type

Small Business

Contact Information for Business Card

Bright Volley Tennis

Owen Whitby
Managing Director

brightvolleyracquets@mailbox.example
www.brightvolleyracquets.com.au
0491 726 305

Racquet Restringing/Tennis Strings/Accessories

Requirements
Must have
• Must have my logo and card must be black

```html
<!DOCTYPE html>
<html lang="en">
<head>
<meta charset="utf-8">
<title>Bright Volley Tennis – Business Card</title>
<link rel="stylesheet" href="https://fonts.googleapis.com/css2?family=Open+Sans:wght@400;600;700&display=swap">
<style>
  :root {
    --backdrop: #d8d5d0;
    --card: #070707;
    --lime: #b5d334;
    --white: #ffffff;
    --rule: #6b6b6b;
  }
  * { box-sizing: border-box; margin: 0; padding: 0; }
  html, body {
    width: 1200px;
    height: 750px;
    overflow: hidden;
    background: var(--backdrop);
    font-family: "Open Sans", Arial, sans-serif;
  }
  .card {
    position: absolute;
    left: 75px;
    top: 75px;
    width: 1050px;
    height: 600px;
    border-radius: 42px;
    background: var(--card);
    color: var(--white);
    overflow: hidden;
  }
  .brand {
    position: absolute;
    left: 48px;
    top: 176px;
    display: flex;
    align-items: center;
    gap: 16px;
  }
  .brand-dot {
    width: 38px;
    height: 38px;
    border-radius: 50%;
    background: var(--lime);
  }
  .brand-name {
    font-weight: 700;
    font-size: 44px;
    color: var(--lime);
    letter-spacing: 0.5px;
    line-height: 1;
  }
  .services {
    position: absolute;
    right: 37px;
    top: 68px;
    list-style: none;
    text-align: right;
    font-size: 29px;
    line-height: 40px;
  }
  .services li::before {
    content: "";
    display: inline-block;
    width: 9px;
    height: 9px;
    background: var(--white);
    margin-right: 12px;
    vertical-align: 6px;
  }
  .person {
    position: absolute;
    left: 38px;
    top: 452px;
    color: var(--lime);
    white-space: nowrap;
  }
  .person-name { font-weight: 700; font-size: 31px; }
  .person-role { font-size: 24px; margin-left: 10px; }
  .divider {
    position: absolute;
    left: 38px;
    right: 37px;
    top: 501px;
    height: 2px;
    background: var(--rule);
  }
  .contacts {
    position: absolute;
    left: 38px;
    right: 37px;
    top: 508px;
    display: flex;
    justify-content: space-between;
    list-style: none;
    font-size: 19px;
    line-height: 34px;
    white-space: nowrap;
  }
  .contacts li { display: flex; align-items: center; gap: 8px; flex-shrink: 0; }
  .contacts svg { width: 20px; height: 20px; fill: var(--lime); stroke: var(--lime); flex-shrink: 0; }
</style>
</head>
<body>
  <main class="card">
    <div class="brand">
      <span class="brand-dot"></span>
      <span class="brand-name">Bright Volley Tennis</span>
    </div>

    <ul class="services">
      <li>Racquet Restringing</li>
      <li>Tennis Strings</li>
      <li>Accessories</li>
    </ul>

    <p class="person">
      <span class="person-name">Owen Whitby,</span><span class="person-role">Managing Director</span>
    </p>

    <div class="divider"></div>

    <ul class="contacts">
      <li>
        <svg viewBox="0 0 24 24" aria-hidden="true"><path stroke="none" d="M2 9c0-3 4-5 10-5s10 2 10 5v2h-5V9H7v2H2zM6 12h12l3 8H3z"/><circle cx="12" cy="15.5" r="2.2" fill="#070707" stroke="none"/></svg>
        <span>0491 726 305</span>
      </li>
      <li>
        <svg viewBox="0 0 24 24" aria-hidden="true"><rect x="2" y="5" width="20" height="14" fill="none" stroke-width="2"/><path d="M2 5l10 8 10-8" fill="none" stroke-width="2"/></svg>
        <span>brightvolleyracquets@mailbox.example</span>
      </li>
      <li>
        <svg viewBox="0 0 24 24" aria-hidden="true"><circle cx="12" cy="12" r="10" fill="none" stroke-width="2"/><path d="M2 12h20M12 2c-4 4-4 16 0 20M12 2c4 4 4 16 0 20" fill="none" stroke-width="1.6"/></svg>
        <span>www.brightvolleyracquets.com.au</span>
      </li>
    </ul>
  </main>
</body>
</html>
```